Letterhead for a German Distribution/Manufacturing Company

We need a professional Letterhead in a unique Design.
not to playful.
The Letterhead has to show show that we are a international company with headquater in Germany.
all details like adress, Vat Tax Number, Bank Accout, Eori, email, Company number has to be on the Letterhead.
for example use: VAT TAX DE5470318 Bank Account: Kestrel Bank IBAN DE412058731ß204683 Swift: MORV0417352 EORI 3150428697 Company Number: HRB 51806 Adress: VOLMINTA UG Ahornweg 7 Postal Code 06384 City Brackwald Country: Germany Email: info@volminta-example.com
the design can be colored but doesnt have to be
Industry/Entity Type
Manufacturing and international distribution
Requirements
Must have
- show that we are a international company with headquater in Germany. our company infos and logo

```html
<!DOCTYPE html>
<html lang="en">
<head>
<meta charset="utf-8">
<title>VOLMINTA UG – Letterhead</title>
<link href="https://fonts.googleapis.com/css2?family=Saira:wght@300;400;600&display=swap" rel="stylesheet">
<style>
  :root {
    --paper: #ffffff;
    --ink: #2a2a2a;
    --ink-soft: #3c3c3c;
    --rule: #d5d8d8;
    --watermark: #f5f5f5;
    --notch-edge: #d6d7d7;
    --notch-fill: #727270;
  }
  * { margin: 0; padding: 0; box-sizing: border-box; }
  html, body { width: 919px; height: 1200px; overflow: hidden; background: var(--paper); }
  body { font-family: "Saira", sans-serif; color: var(--ink); }
  .letterhead { position: relative; width: 919px; height: 1200px; background: var(--paper); }

  .brand { position: absolute; left: 60px; top: 38px; display: flex; align-items: center; gap: 12px; }
  .brand-dot { width: 34px; height: 34px; border-radius: 50%; background: var(--ink); }
  .brand-name { font-size: 38px; font-weight: 400; letter-spacing: 0.5px; color: var(--ink); line-height: 1; }

  .contact { position: absolute; right: 35px; top: 52px; text-align: right; font-size: 15px; font-weight: 300; font-style: normal; line-height: 25px; color: var(--ink-soft); letter-spacing: 0.2px; }
  .contact b { font-weight: 600; color: var(--ink); }
  .header-rule { position: absolute; left: 353px; right: 0; top: 104px; height: 3px; background: var(--rule); }

  .watermark { position: absolute; left: 374px; top: 530px; width: 300px; height: 300px; border-radius: 50%; background: var(--watermark); }

  .company-details { position: absolute; left: 0; right: 0; top: 1052px; text-align: center; font-size: 15px; font-weight: 300; line-height: 25px; color: var(--ink-soft); letter-spacing: 0.2px; }
  .company-details b { font-weight: 600; color: var(--ink); }

  .footer-notch { position: absolute; left: 0; bottom: 0; width: 919px; height: 40px; }
</style>
</head>
<body>
  <main class="letterhead">
    <header>
      <div class="brand">
        <span class="brand-dot"></span>
        <span class="brand-name">VOLMINTA</span>
      </div>
      <address class="contact">
        <div><b>Address :</b> VOLMINTA UG Ahornweg 7 Postal Code 06384</div>
        <div>City Brackwald Country : Germany &nbsp;|&nbsp; <b>Email :</b> info@volminta-example.com</div>
      </address>
      <div class="header-rule"></div>
    </header>

    <div class="watermark" aria-hidden="true"></div>

    <footer class="company-details">
      <div><b>VAT TAX :</b>&nbsp; DE5470318</div>
      <div><b>Company Number :</b> HRB 51806</div>
      <div><b>Swift :</b> MORV0417352 EORI 3150428697</div>
      <div><b>Bank Account :</b> Kestrel Bank IBAN DE412058731ß204683</div>
    </footer>

    <svg class="footer-notch" viewBox="0 0 919 40" aria-hidden="true">
      <polygon points="153,0 764,0 811,40 108,40" fill="var(--notch-edge)"/>
      <polygon points="173,0 745,0 789,40 130,40" fill="var(--notch-fill)"/>
    </svg>
  </main>
</body>
</html>
```